RWT Fittings Ltd Business Cards

We need a business card with our business logo. We provide window and door installations on high-rises in west coast British Colombia, Canada.

I would like my business information and details on one side of the card, and the other side the company name with logo

Target Market(s)

General Contractors

Industry/Entity Type

Construction

Contact Information for Business Card

one side i want my company name and logo in the dark theme logo that i provided

Requirements
Must have
• Marco Peltieri, 16045518293, RWTFittings@mailbox-demo.com, 1407-5194 Linden Row Burnaby BC, V5H 2K9, Owner & Manager

```html
<!DOCTYPE html>
<html lang="en">
<head>
<meta charset="utf-8">
<title>RWT Fittings Ltd – Business Cards</title>
<link rel="stylesheet" href="https://fonts.googleapis.com/css2?family=Poppins:wght@400;600;700&display=swap">
<style>
  :root {
    --backdrop: #1b1b1b;
    --card: #2a2a2a;
    --card-edge: #242424;
    --accent: #29a8e0;
    --ink: #ffffff;
    --muted: #6d6d6d;
  }
  * { margin: 0; padding: 0; box-sizing: border-box; }
  html, body { width: 1200px; height: 900px; overflow: hidden; }
  body {
    background: var(--backdrop);
    font-family: "Poppins", sans-serif;
    color: var(--ink);
  }
  .card {
    position: absolute;
    left: 250px;
    width: 700px;
    height: 400px;
    background: linear-gradient(135deg, var(--card) 0%, var(--card-edge) 100%);
    border-bottom: 7px solid var(--accent);
  }
  .card--front { top: 30px; }
  .card--back { top: 470px; }

  /* front */
  .brand-front {
    position: absolute;
    inset: 0;
    display: flex;
    align-items: center;
    justify-content: center;
    gap: 22px;
    color: var(--muted);
    font-weight: 600;
  }
  .brand-front .mark { width: 70px; height: 70px; background: var(--muted); }
  .brand-front .name { font-size: 46px; letter-spacing: 4px; line-height: 1; }

  /* back */
  .brand-back {
    position: absolute;
    left: 50px;
    top: 120px;
    width: 240px;
    color: var(--ink);
    font-weight: 600;
  }
  .brand-back .mark { width: 40px; height: 40px; background: var(--accent); margin-bottom: 14px; }
  .brand-back .name-main { font-size: 56px; line-height: 1; letter-spacing: 3px; }
  .brand-back .name-sub { font-size: 20px; letter-spacing: 3px; margin-top: 8px; }
  .divider {
    position: absolute;
    left: 318px;
    top: 70px;
    width: 4px;
    height: 240px;
    background: var(--accent);
  }
  .details {
    position: absolute;
    left: 350px;
    top: 64px;
    font-size: 18px;
    line-height: 1.35;
  }
  .person-name {
    color: var(--accent);
    font-size: 30px;
    font-weight: 700;
    letter-spacing: 1px;
    line-height: 1.1;
  }
  .person-role { font-size: 18px; margin-bottom: 18px; }
  .address { margin-bottom: 16px; }
  .contact { list-style: none; }
  .contact li { display: flex; align-items: center; gap: 10px; }
  .contact svg { width: 16px; height: 16px; flex: none; }
  .domain { color: var(--accent); }
</style>
</head>
<body>

<section class="card card--front" aria-label="Card front">
  <div class="brand-front">
    <span class="mark"></span>
    <span class="name">RWT FITTINGS LTD</span>
  </div>
</section>

<section class="card card--back" aria-label="Card back">
  <div class="brand-back">
    <div class="mark"></div>
    <div class="name-main">RWT</div>
    <div class="name-sub">FITTINGS LTD</div>
  </div>
  <div class="divider"></div>
  <div class="details">
    <p class="person-name">MARCO PELTIERI</p>
    <p class="person-role">Owner &amp; Manager</p>
    <p class="address">1407-5194 Linden Row<br>Burnaby BC, V5H 2K9</p>
    <ul class="contact">
      <li>
        <svg viewBox="0 0 16 16" aria-hidden="true"><path fill="#29a8e0" d="M4 1l2.5 3-1.5 2c1 2 2.5 3.5 4.5 4.5l2-1.5 3 2.5-1.5 2.5C7 13.5 2.5 9 1.5 3z"/></svg>
        604-551-8293
      </li>
      <li>
        <svg viewBox="0 0 16 16" aria-hidden="true"><rect x="1.5" y="3.5" width="13" height="9" fill="none" stroke="#29a8e0" stroke-width="1.5"/><path d="M1.5 3.5l6.5 5 6.5-5" fill="none" stroke="#29a8e0" stroke-width="1.5"/></svg>
        RWTFittings@mailbox-demo.com
      </li>
      <li>
        <svg viewBox="0 0 16 16" aria-hidden="true"><circle cx="8" cy="8" r="6.5" fill="none" stroke="#29a8e0" stroke-width="1.5"/><ellipse cx="8" cy="8" rx="2.8" ry="6.5" fill="none" stroke="#29a8e0" stroke-width="1.2"/><path d="M1.5 8h13" stroke="#29a8e0" stroke-width="1.2"/></svg>
        <span>www.<span class="domain">rwtfittings-demo</span>.com</span>
      </li>
    </ul>
  </div>
</section>

</body>
</html>
```